Web Developer Needs a Business Card Design

I need a personal business card design that represents me as a web developer for potential employers. I would like the background to be a dark color on the front for contrast with my logo and name. The back will have all my information along with a smaller version of the logo. I want something with a modern look and feel, not too conservative. This will be used for potential employers and freelance work.

Industry/Entity Type

Business

Contact Information for Business Card

Front should have my logo and name. The back should have all my personal information which would include: name: Tom Varulek, phone: 570-614-3098, email: tomvarulek@quillbox.net, website url: www.tomvarulek.net, logo, web developer.

Font styles to use
Sans Serif

Requirements
Must have
• Must include my logo. The color palette base color will be the logo color.

```html
<!DOCTYPE html>
<html lang="en">
<head>
<meta charset="UTF-8">
<title>Tom Varulek – Business Card</title>
<link rel="stylesheet" href="https://fonts.googleapis.com/css2?family=Roboto:wght@400;500;700&display=swap">
<style>
  :root {
    --mint: #5fe8c9;
    --mint-deep: #3fd9b4;
    --ink: #050505;
    --ink-soft: #121212;
    --paper: #e4e4e4;
    --white: #f4f4f4;
  }
  html, body {
    margin: 0;
    width: 1200px;
    height: 1200px;
    overflow: hidden;
    background: var(--paper);
    font-family: "Roboto", Arial, sans-serif;
  }
  .canvas {
    position: relative;
    width: 1200px;
    height: 1200px;
  }
  .card {
    position: absolute;
    left: 250px;
    width: 700px;
    height: 400px;
    border-radius: 26px;
    overflow: hidden;
    background: linear-gradient(135deg, var(--ink-soft) 0%, var(--ink) 60%);
    box-shadow: 0 10px 30px rgba(0,0,0,0.18);
  }
  .card--front { top: 150px; }
  .card--back { top: 640px; }

  .brand {
    position: absolute;
    display: flex;
    align-items: center;
    gap: 16px;
    color: var(--mint);
    font-weight: 500;
    white-space: nowrap;
  }
  .brand__dot {
    border-radius: 50%;
    background: var(--mint);
    flex: none;
  }
  .card--front .brand {
    left: 50%;
    top: 50%;
    transform: translate(-50%, -50%);
    font-size: 46px;
  }
  .card--front .brand__dot { width: 44px; height: 44px; }

  .card--back .brand {
    left: 48px;
    top: 150px;
    font-size: 34px;
  }
  .card--back .brand__dot { width: 34px; height: 34px; }

  .card__wave {
    position: absolute;
    inset: 0;
  }
  .identity {
    position: absolute;
    right: 40px;
    top: 34px;
    text-align: right;
  }
  .identity__name {
    margin: 0;
    color: var(--mint);
    font-size: 30px;
    font-weight: 700;
    line-height: 1.1;
  }
  .identity__role {
    margin: 4px 0 0;
    color: var(--white);
    font-size: 15px;
    font-weight: 400;
  }
  .contact {
    position: absolute;
    right: 36px;
    top: 218px;
    margin: 0;
    padding: 0;
    list-style: none;
    text-align: right;
  }
  .contact__item {
    display: flex;
    justify-content: flex-end;
    align-items: center;
    gap: 10px;
    color: var(--ink);
    font-size: 17px;
    line-height: 27px;
  }
  .contact__icon {
    width: 16px;
    height: 16px;
    flex: none;
  }
</style>
</head>
<body>
<main class="canvas">

  <section class="card card--front" aria-label="Card front">
    <div class="brand">
      <span class="brand__dot"></span>
      <span class="brand__name">Tom Varulek</span>
    </div>
  </section>

  <section class="card card--back" aria-label="Card back">
    <svg class="card__wave" viewBox="0 0 700 400" preserveAspectRatio="none" aria-hidden="true">
      <defs>
        <linearGradient id="mintFill" x1="0" y1="0" x2="0" y2="1">
          <stop offset="0" stop-color="#63ecce"/>
          <stop offset="1" stop-color="#3fd9b4"/>
        </linearGradient>
      </defs>
      <path d="M700,90 C560,95 440,150 390,240 C340,330 200,350 0,358 L0,400 L700,400 Z" fill="url(#mintFill)"/>
      <path d="M700,106 C574,111 452,166 402,256 C352,346 212,366 0,374" fill="none" stroke="#050505" stroke-width="7"/>
    </svg>

    <div class="brand">
      <span class="brand__dot"></span>
      <span class="brand__name">Tom Varulek</span>
    </div>

    <header class="identity">
      <h1 class="identity__name">Tom Varulek</h1>
      <p class="identity__role">Web Developer</p>
    </header>

    <ul class="contact">
      <li class="contact__item">570-614-3098
        <svg class="contact__icon" viewBox="0 0 16 16" aria-hidden="true"><path d="M3 1.5h3l1.2 3-1.8 1.2a8 8 0 0 0 4 4L10.6 8l3 1.2v3c0 .8-.7 1.5-1.5 1.4C6.6 13.2 2.8 9.4 2.4 3.9 2.3 2.2 2.3 1.5 3 1.5z" fill="#050505"/></svg>
      </li>
      <li class="contact__item">www.tomvarulek.net
        <svg class="contact__icon" viewBox="0 0 16 16" aria-hidden="true"><circle cx="8" cy="8" r="6.5" fill="none" stroke="#050505" stroke-width="1.5"/><ellipse cx="8" cy="8" rx="2.8" ry="6.5" fill="none" stroke="#050505" stroke-width="1.2"/><path d="M1.5 8h13" stroke="#050505" stroke-width="1.2"/></svg>
      </li>
      <li class="contact__item">tomvarulek@quillbox.net
        <svg class="contact__icon" viewBox="0 0 16 16" aria-hidden="true"><rect x="1" y="3" width="14" height="10" rx="1" fill="#050505"/><path d="M1.5 3.8 8 9l6.5-5.2" fill="none" stroke="#5fe8c9" stroke-width="1.2"/></svg>
      </li>
    </ul>
  </section>

</main>
</body>
</html>
```